Brisk & Summit Product Formulation & Benefits

Brisk and Summit's formulation represents a complex formulation of essential all natural ingredients that reduce stress & anxiety, improve mood, with an elevated mood and euphoric sense of well-being, deliver three stage energy boosters, grass fed bovine collagen and vitamins B6 and B12.
based upon the complexity and the range of physical and mental health benefits we are seeking an animated infographic that will educate consumers on the ingredients and their benefits.

Target Market(s)

Coffee, Hemp and Funcational Beverage Consumers

Industry/Entity Type

Functional Food & Beverage

Requirements
Must have
• cross reference of ingredients to their benefits (see website)
Nice to have
• a concept of a puzzle that comes together, each piece with info on it, that when complete illustrates an image of a healthy lifestyle, coffees beverages, with company logo.

```html
<!DOCTYPE html>
<html lang="en">
<head>
<meta charset="utf-8">
<title>Brisk &amp; Summit – Ingredients &amp; Benefits</title>
<link rel="stylesheet" href="https://fonts.googleapis.com/css2?family=Montserrat:ital,wght@1,700;1,800&display=swap">
<style>
  :root {
    --canvas-w: 1200px;
    --canvas-h: 677px;
    --teal-deep: #2f6e6a;
    --teal-soft: #7fb8ab;
    --cream: #efe6d2;
    --amber: #d9823a;
    --wood: #c8834e;
    --knob: #000000;
    --label: #ffffff;
    --label-shadow: rgba(40, 25, 15, 0.75);
  }
  * { margin: 0; padding: 0; box-sizing: border-box; }
  html, body {
    width: var(--canvas-w);
    height: var(--canvas-h);
    overflow: hidden;
    background: #ffffff;
  }
  .benefits-board {
    position: relative;
    width: var(--canvas-w);
    height: var(--canvas-h);
    overflow: hidden;
  }
  .cafe-scene {
    position: absolute;
    inset: 0;
    background:
      linear-gradient(180deg, transparent 0%, transparent 74%, var(--wood) 76%, #b0703f 92%, #3a2a26 100%),
      radial-gradient(ellipse at 32% 55%, var(--teal-soft) 0%, transparent 35%),
      radial-gradient(ellipse at 78% 55%, var(--amber) 0%, transparent 32%),
      linear-gradient(90deg, var(--teal-deep) 0%, #5a8a66 22%, var(--cream) 55%, #cfe0d3 80%, var(--teal-soft) 100%);
  }
  .puzzle-knobs {
    position: absolute;
    inset: 0;
    width: 100%;
    height: 100%;
  }
  .puzzle-knobs ellipse { fill: var(--knob); }
  .benefit {
    position: absolute;
    transform: translateX(-50%);
    font-family: "Montserrat", sans-serif;
    font-style: italic;
    color: var(--label);
    text-align: center;
    white-space: nowrap;
    text-shadow: 2px 3px 4px var(--label-shadow);
  }
  .benefit__name {
    font-weight: 800;
    font-size: 44px;
    line-height: 54px;
    text-transform: uppercase;
  }
  .benefit__name span { display: block; }
  .benefit__ingredients {
    margin-top: 2px;
    font-weight: 700;
    font-size: 15px;
    line-height: 18px;
    letter-spacing: 0.3px;
  }
  .benefit--energy    { left: 596px;  top: 48px; }
  .benefit--focus     { left: 175px;  top: 120px; }
  .benefit--mood      { left: 1008px; top: 101px; }
  .benefit--calm      { left: 168px;  top: 436px; }
  .benefit--wellbeing { left: 589px;  top: 436px; }
  .benefit--wellbeing .benefit__name { line-height: 52px; }
  .benefit--sleep     { left: 992px;  top: 394px; }
</style>
</head>
<body>
  <main class="benefits-board">
    <div class="cafe-scene" role="img" aria-label="Illustration of a woman and a man chatting at a café table with two layered coffee drinks and a glass of herbal tea, surrounded by plants and shelves"></div>

    <svg class="puzzle-knobs" viewBox="0 0 1200 677" aria-hidden="true">
      <ellipse cx="228" cy="28" rx="56" ry="34"/>
      <ellipse cx="640" cy="0" rx="40" ry="8"/>
      <ellipse cx="1026" cy="16" rx="56" ry="30"/>
      <ellipse cx="4" cy="511" rx="18" ry="52"/>
      <ellipse cx="1170" cy="536" rx="36" ry="62"/>
      <ellipse cx="596" cy="664" rx="56" ry="30"/>
    </svg>

    <section class="benefit benefit--energy">
      <h2 class="benefit__name"><span>Sustained</span><span>Energy</span></h2>
      <p class="benefit__ingredients">Three-stage energy blend · Vitamin B12</p>
    </section>
    <section class="benefit benefit--focus">
      <h2 class="benefit__name"><span>Increased</span><span>Focus</span></h2>
      <p class="benefit__ingredients">Vitamins B6 &amp; B12</p>
    </section>
    <section class="benefit benefit--mood">
      <h2 class="benefit__name"><span>Elevated</span><span>Mood</span></h2>
      <p class="benefit__ingredients">Hemp botanicals · Vitamin B6</p>
    </section>
    <section class="benefit benefit--calm">
      <h2 class="benefit__name"><span>Reduced</span><span>Stress</span></h2>
      <p class="benefit__ingredients">All-natural calming botanicals</p>
    </section>
    <section class="benefit benefit--wellbeing">
      <h2 class="benefit__name"><span>Sense</span><span>of</span><span>Well-Being</span></h2>
      <p class="benefit__ingredients">Grass-fed bovine collagen</p>
    </section>
    <section class="benefit benefit--sleep">
      <h2 class="benefit__name"><span>Restorative</span><span>Sleep</span></h2>
      <p class="benefit__ingredients">Hemp botanicals · Collagen</p>
    </section>
  </main>
</body>
</html>
```